VELORA Brisbane Tiling Service

My name is Milos Brendt i need a business card for a new company. We are wall and floor tilers based in Brisbane, our company is Velorix Brisbane Tiling Service.
We would like a logo from our website used on our cards. Our website is www.velorix.com.au

I would like my Chatterbook and Postwave accounts on my card.

Industry/Entity Type

Business

Colors
0692cd
3176b5
33a6d7
85cae6

```html
<!DOCTYPE html>
<html lang="en">
<head>
<meta charset="utf-8">
<title>Velorix Brisbane Tiling Service – Business Card</title>
<link rel="stylesheet" href="https://fonts.googleapis.com/css2?family=Arimo:wght@400&family=Lato:wght@400;700;900&display=swap">
<style>
  :root {
    --brand-blue: #0692cd;
    --brand-deep: #3176b5;
    --brand-mid: #33a6d7;
    --brand-light: #85cae6;
    --logo-blue: #1d6fb8;
    --ink: #1c1c1c;
    --ink-soft: #4a4a4a;
    --navy: #1b3f63;
    --card-white: #ffffff;
    --card-grey: #ebebeb;
    --stage: #e4e6e9;
  }
  * { box-sizing: border-box; margin: 0; padding: 0; }
  html, body { width: 1200px; height: 997px; overflow: hidden; }
  body {
    background: var(--stage);
    font-family: "Lato", Arial, sans-serif;
    position: relative;
  }
  .card {
    position: absolute;
    width: 760px;
    height: 434px;
    left: 220px;
    border-radius: 22px;
    overflow: hidden;
    box-shadow: 0 6px 18px rgba(0,0,0,0.18);
  }
  .card-back { top: 60px; }
  .card-front { top: 524px; }

  .tile-texture { position: absolute; inset: 0; }
  .card-back .tile-texture {
    background: radial-gradient(ellipse at 40% 35%, var(--brand-light) 0%, var(--brand-mid) 55%, var(--brand-deep) 130%);
  }
  .card-front .tile-texture {
    background: radial-gradient(ellipse at 45% 40%, var(--card-white) 0%, #f5f5f5 50%, var(--card-grey) 110%);
  }

  /* Logo lockup */
  .brand { position: absolute; display: flex; align-items: center; }
  .brand-square { flex: none; }
  .brand-text { display: flex; flex-direction: column; font-family: "Arimo", Arial, sans-serif; font-weight: 400; }
  .brand-name { line-height: 0.9; letter-spacing: -0.5px; }
  .brand-tagline { line-height: 1.1; }

  .card-back .brand { left: 120px; top: 125px; }
  .card-back .brand-square { width: 150px; height: 150px; background: var(--card-white); margin-right: 22px; }
  .card-back .brand-name { font-size: 104px; color: var(--card-white); }
  .card-back .brand-tagline { font-size: 40px; color: var(--navy); margin-top: 6px; }

  .card-front .brand { left: 180px; top: 60px; }
  .card-front .brand-square { width: 92px; height: 92px; background: var(--logo-blue); margin-right: 14px; }
  .card-front .brand-name { font-size: 64px; color: var(--logo-blue); }
  .card-front .brand-tagline { font-size: 24px; color: var(--ink); margin-top: 2px; }

  /* Identity block */
  .identity { position: absolute; right: 46px; top: 170px; text-align: right; }
  .person-name { font-weight: 900; font-size: 22px; color: var(--logo-blue); }
  .person-role { font-size: 17px; color: var(--ink-soft); margin-top: 4px; }
  .since { font-weight: 900; font-size: 23px; color: var(--ink); margin-top: 4px; }

  .rule { position: absolute; height: 3px; background: var(--logo-blue); }
  .rule-right { left: 380px; right: 40px; top: 270px; }
  .rule-left { left: 40px; width: 340px; top: 300px; }

  .contact-list, .social-list { position: absolute; list-style: none; }
  .contact-list { left: 46px; top: 318px; }
  .social-list { left: 400px; top: 290px; }
  .contact-list li, .social-list li {
    display: flex; align-items: center; gap: 12px;
    font-weight: 700; font-size: 17px; color: var(--ink-soft);
    height: 34px;
  }
  .icon { width: 22px; height: 22px; flex: none; }
  .social-dot { width: 14px; height: 14px; border-radius: 50%; background: var(--logo-blue); margin: 0 4px; flex: none; }
</style>
</head>
<body>

  <section class="card card-back" aria-label="Business card back">
    <div class="tile-texture" role="img" aria-label="Soft blue tiled mosaic background texture"></div>
    <div class="brand">
      <div class="brand-square"></div>
      <div class="brand-text">
        <span class="brand-name">velorix</span>
        <span class="brand-tagline">brisbane tiling service</span>
      </div>
    </div>
  </section>

  <section class="card card-front" aria-label="Business card front">
    <div class="tile-texture" role="img" aria-label="Subtle light grey tiled mosaic background texture"></div>

    <div class="brand">
      <div class="brand-square"></div>
      <div class="brand-text">
        <span class="brand-name">velorix</span>
        <span class="brand-tagline">brisbane tiling service</span>
      </div>
    </div>

    <div class="identity">
      <p class="person-name">Milos Brendt</p>
      <p class="person-role">Owner / Founder</p>
      <p class="since">Since 1996</p>
    </div>

    <div class="rule rule-right"></div>
    <div class="rule rule-left"></div>

    <ul class="social-list">
      <li><span class="social-dot"></span>postwave.com/Infovelorix</li>
      <li><span class="social-dot"></span>chatterbook.com/Velorix-Brisbane</li>
    </ul>

    <ul class="contact-list">
      <li>
        <svg class="icon" viewBox="0 0 22 22" aria-hidden="true">
          <rect x="5" y="2" width="12" height="18" rx="2" fill="none" stroke="var(--logo-blue)" stroke-width="2"/>
          <line x1="9" y1="17" x2="13" y2="17" stroke="var(--logo-blue)" stroke-width="1.5"/>
        </svg>
        07 3555 0142
      </li>
      <li>
        <svg class="icon" viewBox="0 0 22 22" aria-hidden="true">
          <rect x="2" y="5" width="18" height="13" fill="var(--logo-blue)"/>
          <polyline points="2,5 11,12 20,5" fill="none" stroke="#fff" stroke-width="1.5"/>
        </svg>
        info@velorix.com.au
      </li>
      <li>
        <svg class="icon" viewBox="0 0 22 22" aria-hidden="true">
          <g fill="none" stroke="var(--logo-blue)" stroke-width="2.2" stroke-linecap="round">
            <path d="M9 13 L13 9"/>
            <path d="M10 7 L12 5 a3.5 3.5 0 0 1 5 5 L15 12"/>
            <path d="M12 15 L10 17 a3.5 3.5 0 0 1 -5 -5 L7 10"/>
          </g>
        </svg>
        www.velorix.com.au
      </li>
    </ul>
  </section>

</body>
</html>
```